Website for legal expungement services with button to qualify/disqualify potential clients

Brightpath Record Renewal, LLC is a law firm focusing in legal expungement servcies (allowing people to erase criminal court records, police records, proseution files, etc). I want a more modern look which exudes confidence in the services. I am looking for a clean website that looks very polished. I want to keep the pages to a minimum, as I want the page not so much to answer questions, but to direct traffic to contact the law office. I would like the main focus point to be an button which would take a client through a series of questions to see if they would qualify for the services; this serves two purposes 1) to collect contact info for future marketing via email and 2) eliminate individuals who we are currently unable to help. A current theme that I have played around with are "Change so much, you'll need to reintroduce yourself" alongside a picture of a guys hand outstretched.
On the landing page, I would like a very brief and to the point explanation of what the service would be (i.e. "Leave your past in the past; expunge all your criminal records" ), followed by a list of benefits that it provides. (NB: included is a file "law post card-02" that includes the main benefits to expungement). Also included are two logo files for a more updated logo I currently use ("BRR Logo" and BRR Logo2") (NB: I'm open to revisions on this as well). Lastly, I've had two very minor 'ads' that I did ("postcard back" and "KVT Ad") that I like the idea of.

Target Market(s)

Middle/upper-middle class, mostly male, people with a criminal record or criminal accusation

Industry/Entity Type

Legal Services

Coding

Coded - Design and coding required

Requirements
Must have
• Button that attracts attention up front (possibly stand out coloring) to click to open up a series of questions to qualify/eliminate prospects, and simultaneously gather their info. Also, must be mobile friendly.

```html
<!DOCTYPE html>
<html lang="en">
<head>
<meta charset="utf-8">
<title>Brightpath Record Renewal</title>
<link href="https://fonts.googleapis.com/css2?family=Playfair+Display:wght@700&family=Roboto:wght@400;500;700&display=swap" rel="stylesheet">
<style>
:root{
  --navy:#0f3a73;
  --navy-dark:#0b2f5e;
  --gold:#d4a52a;
  --pink:#d6337a;
  --ink:#1f2328;
  --muted:#444;
  --field:#efefef;
  --line:#d9dde3;
  --black:#0a0a0a;
}
*{box-sizing:border-box;margin:0;padding:0}
html,body{width:1200px;height:4081px;overflow:hidden}
body{font-family:'Roboto',sans-serif;color:var(--ink);background:#fff;position:relative}
.abs{position:absolute}
.serif{font-family:'Playfair Display',serif;font-weight:700}
svg{display:block}

/* top bar */
.topbar{top:0;left:0;width:1200px;height:41px;background:var(--navy);color:#fff;font-size:14px}
.topbar .item{position:absolute;top:12px;display:flex;align-items:center;gap:8px}
.topbar .follow{right:112px;font-weight:500}
.dots{position:absolute;top:13px;right:111px;display:flex;gap:10px}
.dot{width:12px;height:12px;border-radius:50%;background:#fff}

/* header */
.header{top:41px;left:0;width:1200px;height:81px;background:#fff;border-bottom:1px solid #eee}
.brand{position:absolute;left:111px;top:22px;display:flex;align-items:center;gap:12px}
.brand .sq{width:14px;height:14px;background:var(--navy)}
.brand .name{font-family:'Playfair Display',serif;font-weight:700;color:var(--navy);font-size:16px;letter-spacing:1px;line-height:1.1;text-transform:uppercase;width:220px}
.nav{position:absolute;right:111px;top:30px;display:flex;gap:30px;font-size:15px}
.nav a{color:#222;text-decoration:none}
.nav a.active{color:var(--gold);border-bottom:2px solid var(--navy);padding-bottom:6px}

/* hero */
.hero{top:122px;left:0;width:1200px;height:593px;background:linear-gradient(120deg,#b9bcc2 0%,#7f8794 35%,#4a5a78 55%,#9aa0a8 80%,#cfd0d2 100%)}
.hero .shade{position:absolute;inset:0;background:rgba(10,20,40,.35)}
.hero h1{position:absolute;top:168px;left:0;width:1200px;text-align:center;color:#fff;font-size:41px;line-height:46px;text-transform:uppercase}
.hero p{position:absolute;top:278px;left:290px;width:620px;text-align:center;color:#fff;font-size:17px;line-height:29px;font-weight:500}
.btn{display:inline-flex;align-items:center;justify-content:center;gap:10px;color:#fff;font-weight:700;text-transform:uppercase;font-size:16px}
.hero .btn{position:absolute;top:357px;left:466px;width:266px;height:53px;background:var(--pink);border-radius:2px}

/* benefits */
.section-title{position:absolute;left:0;width:1200px;text-align:center;font-size:35px;text-transform:uppercase;color:var(--ink)}
.section-title span{color:var(--navy)}
.benefits-intro{top:845px;left:210px;width:780px;text-align:center;font-size:15px;line-height:26px;color:var(--muted)}
.benefit{position:absolute;width:237px;height:198px;border:1px solid var(--line);padding:5px}
.benefit .in{width:100%;height:100%;border:1px solid var(--line);display:flex;flex-direction:column;align-items:center;justify-content:flex-end;padding:0 14px 26px;text-align:center;font-size:15px;line-height:23px;color:#333}
.benefit svg{margin-bottom:12px}
.benefit.on{border:2px solid var(--navy);background:var(--navy)}
.benefit.on .in{border-color:#fff;color:#fff;padding-bottom:22px}

/* cases */
.cases-photo{top:1452px;left:0;width:596px;height:509px;background:linear-gradient(135deg,#e9e4dc 0%,#c8bfb2 45%,#5a4b3c 75%,#2b2420 100%)}
.cases{top:1452px;left:596px;width:604px;height:509px;background:var(--gold);color:#fff}
.cases h2{position:absolute;left:109px;top:80px;font-size:35px;text-transform:uppercase}
.cases ul{list-style:none;position:absolute;left:109px;top:163px;width:400px}
.cases li{display:flex;gap:16px;align-items:center;font-size:15.5px;line-height:26px;margin-bottom:17px}
.cases li svg{flex:none}
.cases .btn{position:absolute;left:109px;top:376px;width:170px;height:42px;background:var(--navy);font-size:14px;border-radius:2px}

/* services */
.card{position:absolute;top:2114px;width:474px;height:416px;background:#fff;border:1px solid #e4e4e4;border-radius:6px;box-shadow:0 4px 14px rgba(0,0,0,.08)}
.card .ph{position:absolute;left:11px;top:8px;width:452px;height:310px;border-radius:2px}
.card h3{position:absolute;left:0;top:356px;width:100%;text-align:center;font-size:20px;font-weight:500}

/* about */
.about{top:2615px;left:0;width:1200px;height:547px;background:linear-gradient(90deg,var(--navy-dark),var(--navy))}
.about h2{position:absolute;left:111px;top:65px;color:#fff;font-size:35px;text-transform:uppercase}
.about p{position:absolute;left:111px;top:120px;width:455px;color:#fff;font-size:15.5px;line-height:25.6px;text-align:justify}
.about .btn{position:absolute;left:111px;top:430px;width:169px;height:43px;background:var(--gold);font-size:14px;border-radius:2px}
.about .circle{position:absolute;left:661px;top:59px;width:428px;height:428px;border-radius:50%;border:3px solid var(--gold);background:radial-gradient(circle at 45% 40%,#e6e2dc 0%,#a89a8a 45%,#3a4660 80%,#2c3550 100%)}

/* contact */
.field{position:absolute;background:var(--field);border:1px solid #e2e2e2;font-size:13px;color:#666;padding:14px 16px}
.submit{position:absolute;top:3527px;left:520px;width:162px;height:47px;background:var(--gold);font-size:14px;border-radius:2px}

/* footer */
.footer{top:3661px;left:0;width:1200px;height:420px;background:var(--black);color:#fff}
.footer .brand2{position:absolute;left:111px;top:110px;display:flex;align-items:center;gap:12px}
.footer .brand2 .sq{width:14px;height:14px;background:#fff}
.footer .brand2 .name{font-family:'Playfair Display',serif;font-weight:700;font-size:15px;letter-spacing:1px;line-height:1.15;text-transform:uppercase;width:200px}
.footer .soc{position:absolute;left:205px;top:175px;display:flex;gap:18px}
.footer .soc .dot{width:13px;height:13px}
.footer h4{position:absolute;top:88px;font-size:16px;font-weight:700}
.addr{position:absolute;left:449px;top:130px;font-size:13px;line-height:19px}
.addr .row{display:flex;gap:20px;margin-bottom:12px}
.addr b{font-size:11.5px;display:block}
.links{position:absolute;left:690px;top:131px;list-style:none;font-size:13px;line-height:30.5px}
.q{position:absolute;left:854px;top:132px;width:240px;font-size:12.5px;line-height:18px}
.footer .quote{position:absolute;left:854px;top:206px;width:175px;height:46px;background:var(--gold);font-size:14px;border-radius:2px}
.divider{position:absolute;left:111px;top:325px;width:900px;border-top:1px dashed #555}
.goup{position:absolute;left:1010px;top:315px;width:80px;height:20px;border-radius:10px;background:#333;font-size:11px;font-weight:700;display:flex;align-items:center;justify-content:center;gap:4px}
.chat{position:absolute;left:1114px;top:300px;width:36px;height:36px;border-radius:50%;background:var(--navy);display:flex;align-items:center;justify-content:center}
.copy{position:absolute;left:111px;top:371px;font-size:13px}
.legal{position:absolute;right:112px;top:371px;font-size:13px}
</style>
</head>
<body>

<div class="abs topbar">
  <div class="item" style="left:111px">
    <svg width="13" height="10" viewBox="0 0 13 10"><rect x="0.5" y="0.5" width="12" height="9" fill="#fff"/><path d="M1 1l5.5 4.5L12 1" stroke="#0f3a73" fill="none" stroke-width="1.3"/></svg>
    info@brightpath-renewal.com
  </div>
  <div class="item" style="left:338px">
    <svg width="12" height="12" viewBox="0 0 12 12"><path d="M2.5 1l2 2.5-1 1.2a6 6 0 0 0 3.8 3.8l1.2-1 2.5 2-1 1.5C5 11 1 7 1 2.5z" fill="#fff"/></svg>
    555-014-2290
  </div>
  <div class="item follow" style="right:180px">Follow us</div>
  <div class="dots"><span class="dot"></span><span class="dot"></span><span class="dot"></span><span class="dot"></span></div>
</div>

<header class="abs header">
  <div class="brand"><span class="sq"></span><span class="name">Brightpath Record Renewal</span></div>
  <nav class="nav">
    <a class="active" href="#">HOME</a><a href="#">ABOUT US</a><a href="#">SERVICES</a><a href="#">BENEFITS</a><a href="#">CASES QUALIFY</a><a href="#">CONTACT US</a>
  </nav>
</header>

<section class="abs hero">
  <div role="img" aria-label="Man in a blue blazer extending his hand for a handshake" style="position:absolute;inset:0"></div>
  <div class="shade"></div>
  <h1 class="serif">Change so much, you'll need<br>to reintroduce yourself</h1>
  <p>Lorem ipsum dolor sit amet, consectetur adipiscing elit, sed do eiusmod tempor incididunt ut labore et dolore magna enim ad minim aliqua.</p>
  <a class="btn">Book an appointment
    <svg width="15" height="15" viewBox="0 0 16 16"><circle cx="8" cy="8" r="8" fill="#fff"/><path d="M6.5 4.5L10 8l-3.5 3.5" stroke="#d6337a" stroke-width="2" fill="none"/></svg>
  </a>
</section>

<h2 class="section-title serif" style="top:790px">Our <span>Benefits</span></h2>
<p class="abs benefits-intro">Brightpath Record Renewal is a "5-star rated firm, which has been formed with the passing of the New Mexico Expungement law of 2020. It is a subdivision of the Halvorsen Law Firm, and since its creation has helped over 100 New Mexican citizens successfully expunge their criminal records.</p>

<div class="benefit on" style="left:111px;top:948px"><div class="in">
  <svg width="70" height="64" viewBox="0 0 70 64" fill="none" stroke="#fff" stroke-width="2"><rect x="14" y="14" width="40" height="22" rx="2" transform="rotate(-15 34 25)"/><circle cx="34" cy="25" r="6"/><path d="M6 46c8-6 16-6 24-2l12 2c3 1 3 5 0 5H28M10 58c10-4 22-2 32-4l18-10c3-2 6 2 3 4L42 60"/></svg>
  More and better job opportunities leading to highter income</div></div>
<div class="benefit" style="left:358px;top:948px"><div class="in">
  <svg width="64" height="72" viewBox="0 0 64 72" fill="none" stroke="#0f3a73" stroke-width="2"><path d="M24 4l10 12h-6v50h-8V16h-6z"/><path d="M36 30l12-10 10 10"/><path d="M44 40v26M54 36v30"/><circle cx="10" cy="42" r="4"/><circle cx="20" cy="56" r="4"/><path d="M6 60l18-22"/></svg>
  Loan qualification and better loan rates</div></div>
<div class="benefit" style="left:605px;top:948px"><div class="in">
  <svg width="60" height="70" viewBox="0 0 60 70" fill="none" stroke="#0f3a73" stroke-width="2"><path d="M30 4l22 8v18c0 16-10 26-22 32C18 56 8 46 8 30V12z"/><circle cx="30" cy="26" r="6"/><path d="M20 44c2-7 18-7 20 0"/><circle cx="44" cy="52" r="8"/><path d="M40 52l3 3 5-6"/></svg>
  Protecting your privacy</div></div>
<div class="benefit" style="left:853px;top:948px"><div class="in">
  <svg width="72" height="64" viewBox="0 0 72 64" fill="none" stroke="#0f3a73" stroke-width="2"><path d="M16 18l20-10 20 10-20 10z"/><path d="M24 22v10c6 4 18 4 24 0V22"/><rect x="10" y="30" width="52" height="24" rx="2"/><path d="M4 58h64"/></svg>
  Brtter Education opportunities</div></div>

<div class="benefit" style="left:111px;top:1173px"><div class="in">
  <svg width="72" height="70" viewBox="0 0 72 70" fill="none" stroke="#0f3a73" stroke-width="2.4"><rect x="22" y="6" width="16" height="28" rx="2" transform="rotate(45 30 20)"/><path d="M36 28l24 24"/><path d="M6 60h34v6H6z"/><path d="M10 60v-6h26v6"/></svg>
  Removing the stigma of having a criminal record</div></div>
<div class="benefit" style="left:358px;top:1173px"><div class="in">
  <svg width="72" height="70" viewBox="0 0 72 70" fill="none" stroke="#0f3a73" stroke-width="2"><path d="M8 34L30 12l22 22"/><path d="M14 30v32h32V30"/><rect x="24" y="46" width="10" height="16"/><rect x="18" y="34" width="7" height="7"/><rect x="35" y="34" width="7" height="7"/><path d="M44 44l10-10 12 12v16H46"/></svg>
  More options for Housing</div></div>
<div class="benefit" style="left:605px;top:1173px"><div class="in">
  <svg width="60" height="70" viewBox="0 0 60 70" fill="none" stroke="#0f3a73" stroke-width="2"><path d="M16 6h28v18c0 10-6 16-14 16S16 34 16 24z"/><path d="M16 12H6c0 10 4 14 10 14M44 12h10c0 10-4 14-10 14"/><path d="M30 40v12M20 52h20v8H20z"/><path d="M30 15l2 4 4 .5-3 3 1 4-4-2-4 2 1-4-3-3 4-.5z"/></svg>
  Qualifying for government assistance Programs</div></div>
<div class="benefit" style="left:853px;top:1173px"><div class="in">
  <svg width="70" height="70" viewBox="0 0 70 70" fill="none" stroke="#0f3a73" stroke-width="2"><rect x="8" y="6" width="36" height="52" rx="2"/><path d="M16 18h20M16 28h20M16 38h14"/><path d="M48 30l14 5v10c0 9-6 14-14 18-8-4-14-9-14-18V35z"/><path d="M42 46l4 4 8-8"/></svg>
  Lower Insurance Premiums</div></div>

<div class="abs cases-photo" role="img" aria-label="Lawyer handing a document across a desk with a gavel and notepad"></div>
<section class="abs cases">
  <h2 class="serif">Cases Qualify</h2>
  <ul>
    <li><svg width="14" height="14" viewBox="0 0 14 14"><circle cx="7" cy="7" r="6" stroke="#fff" fill="none" stroke-width="1.5"/><path d="M4 7l2 2 4-4" stroke="#fff" fill="none" stroke-width="1.5"/></svg>Lorem ipsum dolor sit amett consectetur adipiscing iusmodincididunt ut labore et dolore magna aliqu</li>
    <li><svg width="14" height="14" viewBox="0 0 14 14"><circle cx="7" cy="7" r="6" stroke="#fff" fill="none" stroke-width="1.5"/><path d="M4 7l2 2 4-4" stroke="#fff" fill="none" stroke-width="1.5"/></svg>Lorem ipsum dolor sit amett consectetur adipiscing iusmodincididunt ut labore et dolore magna aliqu</li>
    <li><svg width="14" height="14" viewBox="0 0 14 14"><circle cx="7" cy="7" r="6" stroke="#fff" fill="none" stroke-width="1.5"/><path d="M4 7l2 2 4-4" stroke="#fff" fill="none" stroke-width="1.5"/></svg>Lorem ipsum dolor sit amett consectetur adipiscing iusmodincididunt ut labore et dolore magna aliqu</li>
  </ul>
  <a class="btn">Learn more
    <svg width="14" height="14" viewBox="0 0 16 16"><circle cx="8" cy="8" r="8" fill="#fff"/><path d="M6.5 4.5L10 8l-3.5 3.5" stroke="#0f3a73" stroke-width="2" fill="none"/></svg>
  </a>
</section>

<h2 class="section-title serif" style="top:2036px">Our Services</h2>
<div class="card" style="left:120px">
  <div class="ph" role="img" aria-label="Lawyers reviewing an open book and signing papers at a desk" style="background:linear-gradient(135deg,#3b4354 0%,#6b6f78 40%,#c9c4bb 75%,#e8e6e2 100%)"></div>
  <h3>Leave your Past in the Past</h3>
</div>
<div class="card" style="left:607px">
  <div class="ph" role="img" aria-label="Person holding an open file folder in an office" style="background:linear-gradient(135deg,#bfc0c2 0%,#8e8a84 40%,#6a5a48 65%,#d8d8d8 100%)"></div>
  <h3>Expunge all Your Criminal Records</h3>
</div>

<section class="abs about">
  <h2 class="serif">About Us</h2>
  <p>Lorem ipsum dolor sit amet, consectetur adipiscing elit, sed do eiusmod tempor incididunt ut labore et dolore magna aliqua. Ut enim ad minim veniam, quis nostrud exercitation ullamco laboris nisi ut aliquip ex ea commodo consequat. Duis aute irure dolor in reprehenderit in voluptate velit esse cillum dolore eu fugiat nulla pariatur. Excepteur sint occaecat cupidatat non proident, sunt in culpa qui officia deserunt mollit anim id est lLorem ipsum dolor sit amet, consectetur adipiscing elit, sed do eiusmod tempor incididunt ut labore et dolore magna aliqua. Ut enim ad minim veniam, quis nostrud exercitation ullamco laboris nisi ut aliquip ex ea commodo consequatDuis aute irure dolor in reprehenderit.</p>
  <a class="btn">Learn more
    <svg width="14" height="14" viewBox="0 0 16 16"><circle cx="8" cy="8" r="8" fill="#fff"/><path d="M6.5 4.5L10 8l-3.5 3.5" stroke="#d4a52a" stroke-width="2" fill="none"/></svg>
  </a>
  <div class="circle" role="img" aria-label="Team of lawyers working together around a laptop"></div>
</section>

<h2 class="section-title serif" style="top:3236px">Get in Touch</h2>
<div class="field" style="left:182px;top:3305px;width:273px;height:44px">Name *</div>
<div class="field" style="left:464px;top:3305px;width:273px;height:44px">Email *</div>
<div class="field" style="left:745px;top:3305px;width:273px;height:44px">Phone Number *</div>
<div class="field" style="left:182px;top:3370px;width:836px;height:125px">Message *</div>
<a class="btn submit">Submit now</a>

<footer class="abs footer">
  <div class="brand2"><span class="sq"></span><span class="name">Brightpath Record Renewal</span></div>
  <div class="soc"><span class="dot"></span><span class="dot"></span><span class="dot"></span></div>

  <h4 style="left:449px">Our Address</h4>
  <div class="addr">
    <div class="row"><svg width="12" height="12" viewBox="0 0 12 12"><path d="M2.5 1l2 2.5-1 1.2a6 6 0 0 0 3.8 3.8l1.2-1 2.5 2-1 1.5C5 11 1 7 1 2.5z" fill="#d4a52a"/></svg><div><b>Phone</b>555-014-2290</div></div>
    <div class="row"><svg width="13" height="10" viewBox="0 0 13 10"><rect x="0.5" y="0.5" width="12" height="9" fill="#d4a52a"/><path d="M1 1l5.5 4.5L12 1" stroke="#0a0a0a" fill="none" stroke-width="1.2"/></svg><div><b>Email</b>info@brightpath-renewal.com</div></div>
    <div class="row"><svg width="12" height="14" viewBox="0 0 12 14"><path d="M6 13S1 8 1 5a5 5 0 0 1 10 0c0 3-5 8-5 8z" fill="#d4a52a"/><circle cx="6" cy="5" r="1.8" fill="#0a0a0a"/></svg><div><b>Location</b>48 Placeholder Avenue,<br>consectetur adipiscing</div></div>
  </div>

  <h4 style="left:690px">Company</h4>
  <ul class="links"><li>Home</li><li>About Us</li><li>Services</li><li>Benefits</li><li>Cases Qualify</li><li>Contact Us</li></ul>

  <h4 style="left:854px">Stil have questios?</h4>
  <p class="q">Contact us using this form. A representative will aswer your questions as soon as possible.</p>
  <a class="btn quote">Get a quote</a>

  <div class="divider"></div>
  <div class="goup"><svg width="8" height="8" viewBox="0 0 8 8"><path d="M4 0l4 4H5v4H3V4H0z" fill="#fff"/></svg>Go Up</div>
  <div class="chat"><svg width="16" height="14" viewBox="0 0 16 14"><path d="M2 1h12a1 1 0 0 1 1 1v7a1 1 0 0 1-1 1H7l-4 3v-3H2a1 1 0 0 1-1-1V2a1 1 0 0 1 1-1z" fill="#fff"/></svg></div>
  <div class="copy">© 2023 Brightpath Record Renewal &nbsp;|&nbsp; All Rights Reserved</div>
  <div class="legal">Privacy Policy &nbsp;|&nbsp; Cookie Policy &nbsp;|&nbsp; Terms Of Services</div>
</footer>

</body>
</html>
```